Business Card Design Project

We are a construction company in Orange County, CA. We need a two sided business card. We would like the back to be our logo with web URL. Front should included Name, title, address, phone, fax and email address.

our address is
627 West Dorrance Blvd, Suite 308
Anaheim, CA 92718

Our logo files are attached.

Construction

```html
<!DOCTYPE html>
<html lang="en">
<head>
<meta charset="utf-8">
<title>Corvane Business Card</title>
<link rel="stylesheet" href="https://fonts.googleapis.com/css2?family=Open+Sans:ital,wght@0,400;0,600;0,700;0,800;1,700&display=swap">
<style>
  :root {
    --brand-blue: #144b7d;
    --ink: #3a3a3a;
    --swoosh-grey: #b3b3b3;
    --card: #ffffff;
    --backdrop: #e6e6e6;
  }
  * { box-sizing: border-box; margin: 0; padding: 0; }
  html, body { width: 960px; height: 1200px; overflow: hidden; }
  body {
    background: var(--backdrop);
    font-family: "Open Sans", Arial, sans-serif;
    color: var(--ink);
    position: relative;
  }
  .card {
    position: absolute;
    left: 61px;
    width: 839px;
    height: 478px;
    background: var(--card);
    border-radius: 28px;
    overflow: hidden;
    box-shadow: 0 4px 14px rgba(0,0,0,0.25);
  }
  .card--front { top: 92px; }
  .card--back { top: 645px; }
  .card__swooshes { position: absolute; inset: 0; width: 100%; height: 100%; }
  .wordmark {
    position: absolute;
    left: 0; right: 0;
    text-align: center;
    font-weight: 800;
    font-size: 124px;
    line-height: 1;
    letter-spacing: -2px;
    color: var(--brand-blue);
  }
  .card--front .wordmark { top: 75px; }
  .card--back .wordmark { top: 165px; font-size: 136px; }
  .contact {
    position: absolute;
    left: 0; right: 0;
    top: 280px;
    text-align: center;
  }
  .contact__name { font-size: 24px; font-weight: 600; line-height: 1; }
  .contact__title { font-size: 20px; }
  .contact__line { font-size: 20px; margin-top: 12px; line-height: 1.2; }
  .contact__line b { font-style: italic; font-weight: 700; }
  .contact__divider { margin: 0 8px; }
  .contact__address { font-size: 20px; margin-top: 14px; }
  .web-url {
    position: absolute;
    left: 0; right: 0;
    top: 400px;
    text-align: center;
    font-size: 28px;
    font-weight: 700;
  }
</style>
</head>
<body>
  <section class="card card--front">
    <svg class="card__swooshes" viewBox="0 0 839 478" aria-hidden="true">
      <path d="M718,0 H839 V140 C815,72 772,22 718,0 Z" fill="var(--brand-blue)"/>
      <path d="M700,0 C770,25 820,80 839,150" fill="none" stroke="var(--swoosh-grey)" stroke-width="4"/>
      <path d="M0,335 C20,410 68,458 118,478 H0 Z" fill="var(--brand-blue)"/>
      <path d="M0,322 C25,405 78,458 132,478" fill="none" stroke="var(--swoosh-grey)" stroke-width="4"/>
    </svg>
    <div class="wordmark">CORVANE</div>
    <div class="contact">
      <p class="contact__name">Your Name, <span class="contact__title">Designation</span></p>
      <p class="contact__line"><b>p</b> : 1-234-4567<span class="contact__divider">|</span><b>f</b> : 1-234-4567</p>
      <p class="contact__line"><b>e</b> : info@corvanebuild.com<span class="contact__divider">|</span><b>w</b> : www.corvanebuild.com</p>
      <p class="contact__address">627 West Dorrance Blvd, Suite 308, Anaheim, CA 92718</p>
    </div>
  </section>

  <section class="card card--back">
    <div class="wordmark">CORVANE</div>
    <p class="web-url">www.corvanebuild.com</p>
  </section>
</body>
</html>
```